Corvana Tongue Works, LLC

We need a business card that includes information about our business and conveys a reliable business that provides document translation services and interpreters for a variety of corporate and individual clients. We want to come across as professional, reliable, yet approachable. It should include the following on one side:

ESL / ENL Language Classes, Private Lessons, and Online Tutors
PLEXA Training and Testing
Translating & Interpreting Services
Contact us about Over-the-Phone Interpreting in over 200 languages
24/7/365
www.corvanatongue.example

The other side should include (555) 481-3062

Rhoda Pelling, President
482 Garnet Ave., Ste. 219
Indianapolis, IN 40917

Please add USA as part of the address. Also, please add rmpelling@corvanatongueworks.example as the e-mail address. Thank you.

Target Market(s)

Business professionals, their families, the international community

Industry/Entity Type

Business

Contact Information for Business Card

24/7/365
www.corvanatongue.example

(555) 481-3062

Rhoda Pelling, President
482 Garnet Ave., Ste. 219
Indianapolis, IN 40917
USA

Font styles to use
Sans Serif

Colors

Designer to choose colors to be used in the design.

Requirements
Must have
• See project description
• e-mail address and web address
• Phone number
Nice to have
• a globe
• physical address
Should not have
• Should not have the same color scheme as other agencies in our market in Indiana unless it is blue and black. No purple or yellow.

```html
<!DOCTYPE html>
<html lang="en">
<head>
<meta charset="utf-8">
<title>Corvana Tongue Works – Business Card</title>
<link rel="stylesheet" href="https://fonts.googleapis.com/css2?family=Roboto:wght@400;500;700&display=swap">
<style>
  :root {
    --brand-blue: #2a96d6;
    --brand-blue-deep: #1f86c6;
    --ink: #111418;
    --paper: #ffffff;
    --backdrop: #e7e8ea;
  }
  * { box-sizing: border-box; margin: 0; padding: 0; }
  html, body { width: 1200px; height: 930px; overflow: hidden; }
  body {
    background: var(--backdrop);
    font-family: "Roboto", Arial, sans-serif;
    position: relative;
  }
  .card {
    position: absolute;
    width: 560px;
    height: 320px;
    border-radius: 14px;
    overflow: hidden;
    box-shadow: 0 6px 18px rgba(0,0,0,0.18);
  }

  /* Front: services */
  .card--services {
    left: 70px; top: 110px;
    background: var(--brand-blue);
    color: var(--paper);
    text-align: center;
  }
  .brand { display: flex; align-items: center; gap: 14px; }
  .brand__dot { width: 62px; height: 62px; border-radius: 50%; flex: none; }
  .brand__name { font-weight: 500; font-size: 30px; line-height: 1.05; text-align: left; }
  .card--services .brand { justify-content: center; margin-top: 34px; }
  .card--services .brand__dot { background: var(--paper); }
  .card--services .brand__name { color: var(--paper); }
  .rule { width: 440px; height: 1px; margin: 0 auto; background: rgba(255,255,255,0.85); }
  .rule--top { margin-top: 26px; }
  .services { margin: 14px 0 12px; font-size: 15px; line-height: 1.35; }
  .contact-note { margin-top: 12px; font-size: 15px; font-weight: 500; line-height: 1.35; }

  /* Back: contact */
  .card--contact { left: 570px; top: 500px; background: var(--paper); }
  .card--contact .wave { position: absolute; inset: 0; }
  .card--contact .brand { position: absolute; left: 36px; top: 110px; }
  .card--contact .brand__dot { background: var(--brand-blue); width: 58px; height: 58px; }
  .card--contact .brand__name { color: var(--ink); font-size: 24px; }
  .person { position: absolute; right: 34px; top: 30px; text-align: right; }
  .person__name {
    color: var(--brand-blue); font-weight: 700; font-size: 28px;
    text-transform: uppercase; letter-spacing: 0.5px;
  }
  .person__role { color: var(--ink); font-size: 14px; margin-top: 2px; }
  .details {
    position: absolute; right: 26px; top: 176px;
    color: var(--paper); text-align: right; font-size: 13px; line-height: 1.45;
  }
  .details__address { margin-bottom: 10px; }
  .details__row { display: flex; justify-content: flex-end; align-items: center; gap: 8px; }
  .details__row svg { width: 12px; height: 12px; flex: none; }
</style>
</head>
<body>

  <section class="card card--services">
    <div class="brand">
      <span class="brand__dot"></span>
      <span class="brand__name">Corvana<br>Tongue Works, LLC</span>
    </div>
    <div class="rule rule--top"></div>
    <p class="services">
      ESL / ENL Language Classes, Private Lessons, and Online Tutors<br>
      PLEXA Training and Testing<br>
      Translating &amp; Interpreting Services
    </p>
    <div class="rule"></div>
    <p class="contact-note">
      Contact us about Over-the-Phone Interpreting in over 200 languages<br>
      24/7/365
    </p>
  </section>

  <section class="card card--contact">
    <svg class="wave" viewBox="0 0 560 320" preserveAspectRatio="none" aria-hidden="true">
      <path d="M40 320 C240 320 260 100 560 90 L560 320 Z" fill="var(--brand-blue)"/>
      <path d="M70 320 C262 318 282 114 560 104 L560 111 C290 122 272 320 92 320 Z" fill="var(--paper)"/>
      <path d="M0 300 C140 310 250 298 305 196 C262 290 140 300 0 294 Z" fill="var(--brand-blue-deep)"/>
      <path d="M0 284 C120 292 230 280 292 188 C240 268 130 282 0 276 Z" fill="var(--ink)"/>
    </svg>

    <div class="brand">
      <span class="brand__dot"></span>
      <span class="brand__name">Corvana<br>Tongue<br>Works, LLC</span>
    </div>

    <div class="person">
      <p class="person__name">Rhoda Pelling</p>
      <p class="person__role">President</p>
    </div>

    <div class="details">
      <p class="details__address">482 Garnet Ave., Ste. 219<br>Indianapolis, IN 40917 USA</p>
      <p class="details__row">(555) 481-3062
        <svg viewBox="0 0 24 24"><path fill="#fff" d="M6.6 10.8a15 15 0 0 0 6.6 6.6l2.2-2.2a1 1 0 0 1 1-.25 11.4 11.4 0 0 0 3.6.57 1 1 0 0 1 1 1V20a1 1 0 0 1-1 1A17 17 0 0 1 3 4a1 1 0 0 1 1-1h3.5a1 1 0 0 1 1 1c0 1.25.2 2.45.57 3.57a1 1 0 0 1-.25 1z"/></svg>
      </p>
      <p class="details__row">rmpelling@corvanatongueworks.example
        <svg viewBox="0 0 24 24"><rect x="2" y="5" width="20" height="14" rx="2" fill="none" stroke="#fff" stroke-width="2"/><path d="M3 6l9 7 9-7" fill="none" stroke="#fff" stroke-width="2"/></svg>
      </p>
      <p class="details__row">www.corvanatongue.example
        <svg viewBox="0 0 24 24"><circle cx="12" cy="12" r="10" fill="none" stroke="#fff" stroke-width="2"/><path d="M2 12h20M12 2c3 3 3 17 0 20M12 2c-3 3-3 17 0 20" fill="none" stroke="#fff" stroke-width="1.6"/></svg>
      </p>
    </div>
  </section>

</body>
</html>
```